Children’s entertainer/balloon artist Website Home Page and custom landing page

I need a home page design for the home page of a children and family entertainer/balloon twister’s website. I also need a custom landing page for family theatre shows performed by the same entertainer.
It will be a Wordpress website and I need the final artwork in a layer Photoshop file with all the layers clearly named and labeled.

Target Market(s)

The site visitors are mainly mums, aged between early 20’s and late 30’s. Other visitors will included companies for Christmas functions, and event organisers for corporate functions.

Industry/Entity Type

Entertainment

Number of Pages Required

2 page

Font styles to use
Sans Serif

Colors
34a6d7
f37122

Requirements
Must have
• Layout
• I have included a wireframe for the home page layout and the custom landing page for your reference. This is a guide only and I welcome your interpretation with the rough layout provided.
• This website needs to look good on all devices as it will be fully responsive.
• It needs to include a footer area on the page, that has social media and a call to action area included.
• Colours
• The main colours for the site is:
• orange (call to action colour)
• ff6800
• blue/turquoise
• 42abc3
• Pictures
• I have included images of the entertainer/balloon artist for you to use/take inspiration from.
• These images will be included on the website. I want to show lots of people having fun.
• I would like to have elements of the logo used in isolation across the website
• i.e. the octopus figure to be included in the footer or the bird element to be included in the testimonial slider etc.
• Elements to include
• Note: use the images of the entertainer in the boxes on the home page (balloon shows, balloon twisting, balloon workshops, theatre shows (the three little balloon pigs on his head)
Nice to have
Should not have
• Element to avoid
• Stock imagery of balloon sculptures - use images provided.

```html
<!DOCTYPE html>
<html lang="en">
<head>
<meta charset="utf-8">
<title>Benny The Goof – Children's Entertainer</title>
<link href="https://fonts.googleapis.com/css2?family=Fredoka:wght@500;600&family=Open+Sans:ital,wght@0,400;0,600;0,700;0,800;1,400;1,600&display=swap" rel="stylesheet">
<style>
:root{
  --blue:#34a6d7;
  --blue-dark:#1f6f9c;
  --navy:#1b3f63;
  --orange:#f37122;
  --ink:#2d2d2d;
  --muted:#7a7a7a;
  --band:#efefef;
  --line:#d9d9d9;
  --footer:#2b2b2b;
  --white:#ffffff;
}
*{box-sizing:border-box;margin:0;padding:0}
html,body{width:837px;height:1200px;overflow:hidden}
body{background:var(--white);font-family:"Open Sans",Arial,sans-serif;color:var(--ink);position:relative}
.wrap{position:absolute;left:64px;width:712px}

/* header */
.nav{position:absolute;top:30px;left:0;width:837px;height:40px;background:var(--blue);display:flex;align-items:center;z-index:2}
.nav ul{list-style:none;display:flex;width:100%;padding:0 40px}
.nav li{font-size:10px;font-weight:700;color:var(--white);letter-spacing:.3px}
.nav .left{display:flex;gap:26px;flex:1}
.nav .right{display:flex;gap:26px;flex:1;justify-content:flex-end}
.brand{position:absolute;top:4px;left:338px;width:160px;height:96px;background:var(--white);border-radius:10px;z-index:3;display:flex;flex-direction:column;align-items:center;justify-content:center;gap:6px;box-shadow:0 2px 6px rgba(0,0,0,.2)}
.brand .dot{width:30px;height:30px;border-radius:50%;background:var(--orange)}
.brand .name{font-family:"Fredoka",sans-serif;font-weight:600;font-size:19px;color:var(--navy)}

/* hero */
.hero{position:absolute;top:70px;left:0;width:837px;height:363px;background:linear-gradient(180deg,#6cc6ea,#2f94c9)}
.hero-photo{position:absolute;left:60px;top:0;width:480px;height:363px;background:radial-gradient(ellipse at 45% 45%,#f3b8c8 0%,#d78aa6 28%,#4aa9d8 62%,#3594c8 100%)}
.hero-copy{position:absolute;left:572px;top:100px;width:205px;font-family:"Fredoka",sans-serif;font-weight:600;color:var(--white);line-height:1.15}
.hero-copy .who{font-size:32px;color:var(--orange)}
.hero-copy .role{font-size:22px}
.hero-copy .pitch{font-size:21px;margin-top:8px}
.btn{display:inline-block;background:var(--orange);color:var(--white);font-weight:700;border-radius:4px;text-transform:uppercase}
.hero .btn{position:absolute;left:572px;top:252px;width:130px;height:42px;line-height:42px;text-align:center;font-size:15px;font-family:"Fredoka",sans-serif;font-weight:600}
.dots{position:absolute;left:590px;top:312px;display:flex;gap:8px}
.dots span{width:9px;height:9px;border-radius:50%;border:1.5px solid var(--white)}
.dots span.on{background:var(--white)}
.arrow{position:absolute;top:154px;width:34px;height:54px;background:var(--navy);display:flex;align-items:center;justify-content:center}
.arrow.l{left:12px;border-radius:0 27px 27px 0}
.arrow.r{right:12px;border-radius:27px 0 0 27px}

/* section titles */
.title{font-family:"Open Sans",sans-serif;font-weight:800;font-size:22px;letter-spacing:.2px;color:var(--ink);border-bottom:1px solid var(--line);padding-bottom:8px;position:relative}
.title em{font-style:normal;color:var(--orange)}
.title svg{position:absolute;right:0;top:0}

/* testimonials */
.testimonials{top:455px;width:460px}
.quote{display:flex;gap:18px;margin-top:22px}
.avatar{width:72px;height:72px;border-radius:50%;flex:none;background:linear-gradient(135deg,#e9d3c4,#b9907b);border:3px solid var(--white);box-shadow:0 0 0 1px var(--line)}
.qmark{font-family:Georgia,serif;font-size:46px;color:var(--line);line-height:1;margin-top:-4px}
.qbody .name{font-size:10px;font-weight:700;color:var(--orange);text-transform:uppercase}
.qbody .role{font-size:8px;color:var(--muted);margin-bottom:8px}
.qbody p{font-size:9.5px;font-style:italic;color:var(--muted);line-height:1.55}
.qrow{display:flex;gap:8px}
.slide-nav{position:absolute;right:0;top:190px;display:flex;gap:6px}
.slide-nav span{width:16px;height:16px;border-radius:50%;background:var(--line);display:flex;align-items:center;justify-content:center}

.contact{position:absolute;left:570px;top:455px;width:150px;height:155px;background:var(--ink);border-radius:4px;color:var(--white);padding:12px 12px}
.contact h3{font-size:10px;font-weight:800;text-transform:uppercase;line-height:1.3;width:100px}
.contact .make{font-size:10px;font-style:italic;margin-top:22px;color:#cfcfcf}
.contact .phone{font-size:13px;font-weight:700;margin-top:6px;display:flex;align-items:center;gap:5px;white-space:nowrap}
.contact .btn{margin-top:14px;font-size:8px;padding:6px 10px}
.mascot{position:absolute;left:712px;top:432px;width:64px;height:76px;border-radius:30px 30px 8px 8px;background:linear-gradient(180deg,#f3a04f,#34a6d7 60%,#1f6f9c)}

/* about band */
.band{position:absolute;top:684px;left:0;width:837px;height:279px;background:var(--band)}
.about{top:700px;width:460px}
.about .lead{font-size:11.5px;font-weight:700;font-style:italic;margin-top:14px;line-height:1.45}
.about p.body{font-size:9px;color:var(--muted);line-height:1.6;margin-top:10px}
.btn-blue{display:inline-block;background:var(--blue);color:var(--white);font-size:9px;font-weight:700;padding:6px 12px;border-radius:3px;text-transform:uppercase}
.about .btn-blue{margin-top:14px}
.newsletter{position:absolute;top:700px;left:570px;width:206px}
.newsletter .title{font-size:17px}
.newsletter p{font-size:8.5px;color:var(--muted);margin-top:12px;line-height:1.5}
.field{margin-top:8px;height:24px;background:var(--white);border:1px solid var(--line);font-size:9px;color:#a5a5a5;padding:5px 8px}
.newsletter .btn-blue{margin-top:10px}

/* service tiles */
.tiles{top:977px;display:flex;justify-content:space-between}
.tile{width:168px;height:140px;border-radius:3px;position:relative;overflow:hidden;padding:14px}
.tile .art{position:absolute;inset:0}
.tile h4{position:relative;font-family:"Fredoka",sans-serif;font-weight:600;font-size:22px;line-height:1;color:var(--white)}
.tile .btn{position:absolute;left:14px;bottom:16px;font-size:8px;padding:5px 9px}
.t1 .art{background:linear-gradient(160deg,#3d8ac4,#6b4a9e)}
.t2 .art{background:linear-gradient(160deg,#34a6d7,#2a5fa3)}
.t3 .art{background:linear-gradient(160deg,#2a6fb3,#4b3b8c)}
.t4 .art{background:linear-gradient(160deg,#3a7fc0,#6d4f9c)}

/* footer */
.footer{position:absolute;top:1130px;left:0;width:837px;height:70px;background:var(--footer);color:#cfcfcf}
.footer ul{position:absolute;left:64px;top:16px;list-style:none;display:flex;gap:18px;font-size:8.5px;font-weight:700;color:var(--white)}
.footer .copy{position:absolute;left:64px;top:40px;font-size:8px;color:#9a9a9a}
.social{position:absolute;right:61px;top:22px;display:flex;gap:8px}
.social span{width:20px;height:20px;border-radius:50%;background:var(--blue)}
</style>
</head>
<body>

<header>
  <nav class="nav">
    <ul>
      <li class="left"><span>BALLOON SHOWS</span><span>BALLOON TWISTING</span></li>
      <li class="right"><span>THEATRE</span><span>CLIENT REVIEWS</span><span>CONTACT US</span></li>
    </ul>
  </nav>
  <div class="brand"><span class="dot"></span><span class="name">Benny The Goof</span></div>
</header>

<section class="hero">
  <div class="hero-photo" role="img" aria-label="Photo of the entertainer wearing three pink pig balloons on his head"></div>
  <div class="arrow l"><svg width="12" height="18" viewBox="0 0 12 18"><path d="M10 2 3 9l7 7" fill="none" stroke="#fff" stroke-width="3"/></svg></div>
  <div class="arrow r"><svg width="12" height="18" viewBox="0 0 12 18"><path d="M2 2l7 7-7 7" fill="none" stroke="#fff" stroke-width="3"/></svg></div>
  <div class="hero-copy">
    <div class="who">Benny</div>
    <div class="role">The Entertainer,</div>
    <div class="pitch">Will make you laugh like never before!</div>
  </div>
  <a class="btn">About Me</a>
  <div class="dots"><span class="on"></span><span></span></div>
</section>

<section class="wrap testimonials">
  <h2 class="title">CLIENT <em>TESTIMONIALS</em>
    <svg width="24" height="22" viewBox="0 0 24 22"><path d="M3 2h18a2 2 0 0 1 2 2v10a2 2 0 0 1-2 2H10l-6 5v-5H3a2 2 0 0 1-2-2V4a2 2 0 0 1 2-2z" fill="none" stroke="#bdbdbd" stroke-width="1.5"/></svg>
  </h2>
  <div class="quote">
    <div class="avatar" role="img" aria-label="Portrait of a happy parent"></div>
    <div class="qrow">
      <div class="qmark">&ldquo;</div>
      <div class="qbody">
        <div class="name">Jenna Morris</div>
        <div class="role">Happy parent</div>
        <p>Benny was brilliant at our daughter's party. Every child laughed from start to finish, the balloon animals were a huge hit and he kept the whole room smiling. We would book him again in a heartbeat and have already told all our friends about him.</p>
      </div>
    </div>
  </div>
  <div class="slide-nav">
    <span><svg width="6" height="8" viewBox="0 0 6 8"><path d="M5 1 2 4l3 3" fill="none" stroke="#666" stroke-width="1.5"/></svg></span>
    <span><svg width="6" height="8" viewBox="0 0 6 8"><path d="M1 1l3 3-3 3" fill="none" stroke="#666" stroke-width="1.5"/></svg></span>
  </div>
</section>

<aside class="contact">
  <h3>Contact the<br>entertainer</h3>
  <div class="make">Make A Call</div>
  <div class="phone"><svg width="12" height="12" viewBox="0 0 24 24"><path d="M6.6 10.8a15 15 0 0 0 6.6 6.6l2.2-2.2a1 1 0 0 1 1-.25 11.4 11.4 0 0 0 3.6.57 1 1 0 0 1 1 1V20a1 1 0 0 1-1 1A17 17 0 0 1 3 4a1 1 0 0 1 1-1h3.5a1 1 0 0 1 1 1c0 1.25.2 2.45.57 3.57a1 1 0 0 1-.25 1z" fill="#f37122"/></svg>(020) 555-0147</div>
  <a class="btn">Request a call back</a>
</aside>
<div class="mascot" role="img" aria-label="Illustrated octopus mascot wrapped in balloons"></div>

<div class="band"></div>
<section class="wrap about">
  <h2 class="title">ABOUT <em>BENNY THE GOOF</em>
    <svg width="24" height="22" viewBox="0 0 24 22"><path d="M3 2h18a2 2 0 0 1 2 2v10a2 2 0 0 1-2 2H10l-6 5v-5H3a2 2 0 0 1-2-2V4a2 2 0 0 1 2-2z" fill="none" stroke="#bdbdbd" stroke-width="1.5"/></svg>
  </h2>
  <p class="lead">A Kids Entertainer And Balloon Artist Living And Working The South Of The UK, Called Benny</p>
  <p class="body">Benny brings laughter, magic and mountains of balloons to birthday parties, school fairs, family days and festive functions across the south. His shows mix silly comedy, audience games and jaw-dropping balloon creations, so every child goes home with a big smile and a balloon to remember the day. From small parties to large corporate events, each show is tailored to the crowd.</p>
  <a class="btn-blue">Read More</a>
</section>

<section class="newsletter">
  <h2 class="title">NEWSLETTER <em>SIGN UP</em></h2>
  <p>Sign up to our newsletter to get all the latest updates and news from Benny.</p>
  <div class="field">Name</div>
  <div class="field">Email Address</div>
  <a class="btn-blue">Subscribe</a>
</section>

<section class="wrap tiles">
  <article class="tile t1"><div class="art" role="img" aria-label="Photo of the entertainer performing a balloon show"></div><h4>Balloon<br>Shows</h4><a class="btn">Show More</a></article>
  <article class="tile t2"><div class="art" role="img" aria-label="Photo of the entertainer twisting balloons"></div><h4>Balloon<br>Twisting</h4><a class="btn">Show More</a></article>
  <article class="tile t3"><div class="art" role="img" aria-label="Photo of children at a balloon workshop"></div><h4>Balloon<br>Workshops</h4><a class="btn">Show More</a></article>
  <article class="tile t4"><div class="art" role="img" aria-label="Photo of the entertainer on stage in a theatre show"></div><h4>Theater<br>Shows</h4><a class="btn">Show More</a></article>
</section>

<footer class="footer">
  <ul><li>HOME</li><li>BALLOON SHOWS</li><li>BALLOON TWISTING</li><li>THEATRE</li><li>REVIEWS</li><li>CONTACT US</li></ul>
  <div class="copy">&copy; 2015 Brightpark Studio Ltd. All Rights Reserved.</div>
  <div class="social"><span></span><span></span><span></span><span></span></div>
</footer>

</body>
</html>
```